Design a WordPress layout for a home loans company

The home loans company in question is going through a rebrand and needs a new website layout.
Sites they like: http://www.brightkeylending.com.au/
Current logo: Attached.
Colours to be used: As per those used in logo.
Primary: #71aa3d
Secondary: #130e10
Pages to be designed:
- Homepage
- Internal services page
Menu items for display purposes:
- Home
- About Us
- Speak to a Broker
- Articles
- Contact Us
A modern design with simplicity is key.
For copy, dummy text such as Lorem ipsum will be fine.
If you would like anything elso, please ask.
Target Market(s)
25-40 year old
Mostly female
Buying their first home in most cases
Industry/Entity Type
Mortgage Brokerage
Number of Pages Required
2 page

```html
<!DOCTYPE html>
<html lang="en">
<head>
<meta charset="utf-8">
<title>Brightkey Lending – Home Loans</title>
<link href="https://fonts.googleapis.com/css2?family=Lato:ital,wght@0,400;0,700;1,400&family=Quicksand:wght@500;700&family=Tinos:ital,wght@0,700;1,700&display=swap" rel="stylesheet">
<style>
:root{
  --green:#71aa3d;
  --green-dark:#5f9430;
  --ink:#130e10;
  --text:#333333;
  --muted:#666666;
  --light:#f2f2f2;
  --line:#e2e2e2;
  --footer:#2e2e2e;
  --white:#ffffff;
}
*{box-sizing:border-box;margin:0;padding:0}
html,body{width:1200px;height:3261px;overflow:hidden}
body{position:relative;background:var(--white);font-family:"Lato",Arial,sans-serif;color:var(--text)}
.abs{position:absolute}
svg{display:block}

/* header */
.social{top:41px;left:78px;display:flex;gap:12px}
.social span{width:44px;height:44px;border-radius:50%;background:#ececec;display:block}
.brand{top:40px;left:0;width:1200px;text-align:center;font-family:"Quicksand",sans-serif;font-weight:700;font-size:38px;color:var(--green)}
.call{top:40px;left:905px;display:flex;gap:18px;align-items:center}
.call small{display:block;font-size:17px;color:#888}
.call strong{display:block;font-size:25px;font-weight:400;color:var(--text);letter-spacing:.5px}

/* nav */
.nav{top:135px;left:0;width:1200px;height:63px;background:var(--green)}
.nav a{position:absolute;top:19px;font-size:18px;color:var(--white);text-decoration:none}
.nav .search{position:absolute;left:828px;top:11px;width:42px;height:42px;border:2px solid var(--white);border-radius:50%;display:flex;align-items:center;justify-content:center}
.nav .enquire{position:absolute;left:935px;top:0;width:189px;height:63px;background:#2b2b2b;color:var(--white);font-size:19px;font-weight:700;display:flex;align-items:center;justify-content:center}

/* hero */
.hero{top:202px;left:0;width:1200px;height:574px;background:linear-gradient(180deg,#e4e8ea 0%,#c9cfd2 45%,#9aa27c 80%,#6d8a45 100%)}
.hero-badge{top:318px;left:660px;width:364px;height:364px;border-radius:50%;background:rgba(255,255,255,.45);padding:16px}
.hero-badge .inner{width:100%;height:100%;border-radius:50%;background:var(--green);text-align:center;color:var(--white);padding-top:46px}
.hero-badge h1{font-family:"Quicksand",sans-serif;font-weight:700;font-size:41px;line-height:44px}
.hero-badge p{font-size:15px;line-height:24px;margin:12px auto 0;width:300px}
.hero-btn{top:623px;left:732px;width:218px;height:62px;background:var(--ink);color:var(--white);font-size:18px;font-weight:700;display:flex;align-items:center;justify-content:center;clip-path:polygon(8% 0,92% 0,100% 50%,92% 100%,8% 100%,0 50%)}
.dots{top:750px;left:0;width:1200px;display:flex;justify-content:center}
.dots div{background:var(--white);padding:6px 10px;border-radius:8px 8px 0 0;display:flex;gap:8px}
.dots i{width:14px;height:14px;border-radius:50%;border:2px solid #888;display:block}
.dots i.on{background:var(--green);border-color:var(--green)}

/* welcome */
.h2{font-family:"Tinos",serif;font-weight:700;color:var(--ink);text-align:center;width:1200px;left:0}
.welcome-title{top:838px;font-size:38px}
.welcome-title em{font-style:normal;color:var(--green)}
.intro{top:904px;left:260px;width:680px;text-align:center;font-size:14px;line-height:25px;color:var(--muted)}
.subtitle{top:1006px;font-size:29px;font-style:italic}
.feature{top:1084px;width:330px;text-align:center}
.feature .ring{width:126px;height:126px;margin:0 auto;border-radius:50%;border:1px dashed #bbb;display:flex;align-items:center;justify-content:center}
.feature .ring span{width:106px;height:106px;border-radius:50%;background:var(--white);box-shadow:0 2px 6px rgba(0,0,0,.12);display:flex;align-items:center;justify-content:center}
.feature h3{font-family:"Quicksand",sans-serif;font-weight:500;font-size:22px;color:var(--green);margin-top:27px}
.feature p{font-size:14px;line-height:25px;color:var(--muted);margin-top:10px}

/* broker */
.broker{top:1437px;left:0;width:1200px;height:498px;background:var(--light)}
.broker-photo{top:1437px;left:0;width:685px;height:498px;background:linear-gradient(135deg,#f4f4f2 0%,#e6dfd6 50%,#cfc1b0 100%)}
.broker-form{top:1495px;left:707px;width:415px}
.broker-form h2{font-family:"Tinos",serif;font-size:35px;color:var(--ink)}
.broker-form label{display:block;font-size:15px;font-weight:700;color:var(--ink)}
.field{height:55px;background:var(--white);border:1px solid #d8d8d8;font-size:13px;color:#888;padding:18px 14px}
.btn-green{height:54px;background:var(--green);color:var(--white);font-size:17px;display:flex;align-items:center;justify-content:center}

/* blog */
.blog-title{top:1995px;font-size:36px}
.card{top:2083px;width:331px;height:363px;border:1px solid var(--line);background:var(--white)}
.card .thumb{height:187px}
.card .meta{padding:34px 12px 0;font-size:12px;color:#999}
.card .meta i{font-style:italic}
.card h3{font-family:"Quicksand",sans-serif;font-weight:500;font-size:19px;color:var(--green);padding:10px 12px 0}
.card p{font-size:13px;line-height:25px;color:var(--muted);padding:6px 12px 0}

/* newsletter */
.news{top:2511px;left:0;width:600px;height:207px;background:var(--green)}
.news h2{position:absolute;top:40px;left:78px;font-family:"Tinos",serif;font-size:33px;color:var(--white)}
.news .email{position:absolute;top:107px;left:78px;width:446px;height:56px;background:var(--white);border-radius:3px;display:flex;align-items:center;padding-left:10px;font-size:14px;color:#555;gap:14px}
.news .send{position:absolute;right:4px;top:4px;width:56px;height:48px;background:var(--ink);border-radius:3px;display:flex;align-items:center;justify-content:center}
.map{top:2511px;left:600px;width:600px;height:207px;background:linear-gradient(135deg,#eef0e8 0%,#e3e6dc 60%,#d8dde3 100%)}

/* footer */
.footer{top:2718px;left:0;width:1200px;height:543px;background:var(--footer)}
.fcol{top:2780px;width:250px;color:var(--white)}
.fcol h4{font-family:"Tinos",serif;font-size:21px;margin-bottom:34px}
.fbrand{font-family:"Quicksand",sans-serif;font-weight:700;font-size:34px;color:var(--green);margin-bottom:18px}
.fcol p,.fcol li{font-size:14px;line-height:25px}
.fcol a{color:var(--white);font-style:italic;font-weight:700;text-decoration:underline}
.fcol ul{list-style:none}
.contact-row{display:flex;gap:14px;margin-bottom:16px;align-items:flex-start}
.finput{background:var(--white);border-radius:3px;font-size:13px;color:#777;padding:12px;margin-bottom:16px}
.rule{top:3178px;left:0;width:1200px;height:1px;background:#4a4a4a}
.copy{top:3205px;left:0;width:1200px;text-align:center;font-size:14px;color:#ddd}
.copy b{color:var(--white)}
</style>
</head>
<body>

<!-- header -->
<div class="abs social"><span></span><span></span><span></span><span></span></div>
<div class="abs brand">Brightkey Lending</div>
<div class="abs call">
  <svg width="40" height="44" viewBox="0 0 24 24"><path fill="#71aa3d" d="M6.6 10.8c1.4 2.8 3.8 5.1 6.6 6.6l2.2-2.2c.3-.3.7-.4 1-.2 1.1.4 2.3.6 3.6.6.6 0 1 .4 1 1V20c0 .6-.4 1-1 1C10.6 21 3 13.4 3 4c0-.6.4-1 1-1h3.5c.6 0 1 .4 1 1 0 1.3.2 2.5.6 3.6.1.3 0 .7-.2 1l-2.3 2.2z"/></svg>
  <div><small>Call Us Now</small><strong>123 456 7890</strong></div>
</div>

<nav class="abs nav">
  <a style="left:80px">Home</a>
  <a style="left:191px">About Us</a>
  <a style="left:333px">Speak to a Broker</a>
  <a style="left:552px">Articles</a>
  <a style="left:680px">Contact Us</a>
  <span class="search"><svg width="20" height="20" viewBox="0 0 20 20"><circle cx="8" cy="8" r="6" fill="none" stroke="#fff" stroke-width="2"/><path d="M12.5 12.5l5 5" stroke="#fff" stroke-width="2.2" stroke-linecap="round"/></svg></span>
  <span class="enquire">ENQUIRE</span>
</nav>

<!-- hero -->
<div class="abs hero" role="img" aria-label="Photo of a couple embracing in front of a modern new house"></div>
<div class="abs hero-badge"><div class="inner">
  <h1>Make Your<br>Dreams Come<br>True</h1>
  <p>Your family deserves the most comfortable house to live.We help people to start a new life in a new place!</p>
</div></div>
<div class="abs hero-btn">CONTACT US</div>
<div class="abs dots"><div><i></i><i class="on"></i><i></i></div></div>

<!-- welcome -->
<h2 class="abs h2 welcome-title">Welcome to <em>BRIGHTKEY LENDING</em></h2>
<p class="abs intro">Lorem Ipsum is simply dummy text of the printing and typesetting industry. Lorem Ipsum has been the industry's standard dummy text ever since the 1500s, when an unknown printer took a galley of type and scrambled it to make a type specimen book.</p>
<h2 class="abs h2 subtitle">With a Brightkey Lending broker, you’ll have</h2>

<div class="abs feature" style="left:70px">
  <div class="ring"><span><svg width="56" height="56" viewBox="0 0 56 56" fill="none" stroke="#71aa3d" stroke-width="2"><circle cx="32" cy="32" r="16"/><path d="M16 32h32M32 16c-6 6-6 26 0 32M32 16c6 6 6 26 0 32"/><path d="M18 6a9 9 0 0 1 9 9c0 7-9 15-9 15s-9-8-9-15a9 9 0 0 1 9-9z" fill="#fff"/><circle cx="18" cy="15" r="3"/></svg></span></div>
  <h3>Local experts</h3>
  <p>With brokers all across Australia, you can be confident there is a professional near you with in-depth knowledge of your local area.</p>
</div>
<div class="abs feature" style="left:435px">
  <div class="ring"><span><svg width="56" height="56" viewBox="0 0 56 56" fill="none" stroke="#71aa3d" stroke-width="2"><circle cx="28" cy="22" r="14"/><circle cx="28" cy="22" r="9"/><path d="M28 17l1.6 3.3 3.6.5-2.6 2.5.6 3.6-3.2-1.7-3.2 1.7.6-3.6-2.6-2.5 3.6-.5z" fill="#71aa3d"/><path d="M20 33l-5 14 6-3 3 5 4-10M36 33l5 14-6-3-3 5-4-10"/></svg></span></div>
  <h3>Ongoing trusted advice</h3>
  <p>We believe in the power of advice to help you both now and into the future as your circumstances and needs change.</p>
</div>
<div class="abs feature" style="left:800px">
  <div class="ring"><span><svg width="56" height="56" viewBox="0 0 56 56" fill="none" stroke="#71aa3d" stroke-width="2"><rect x="12" y="10" width="28" height="38" rx="2"/><path d="M20 8h12v6H20z" fill="#fff"/><path d="M17 22l2 2 3-4M26 22h9M17 31l2 2 3-4M26 31h9M17 40l2 2 3-4M26 40h6"/><path d="M44 20l4 4-12 14-5 1 1-5z" fill="#fff"/></svg></span></div>
  <h3>Greater choice</h3>
  <p>Financial solutions aren't one-size-fits all, and our extensive range of lenders and products ensures we have the right solution for each individual.</p>
</div>

<!-- find a broker -->
<div class="abs broker"></div>
<div class="abs broker-photo" role="img" aria-label="Photo of a smiling family reading a book together on a white sofa"></div>
<div class="abs broker-form">
  <h2>Find a Local Broker</h2>
  <label style="margin-top:34px">Suburb/town</label>
  <div class="field" style="margin-top:12px">Enter a location</div>
  <label style="margin-top:20px">or postcode</label>
  <div class="field" style="margin-top:12px"></div>
  <div class="btn-green" style="margin-top:44px">FIND BROKER</div>
</div>

<!-- blog -->
<h2 class="abs h2 blog-title">Blog &amp; Articals</h2>
<div class="abs card" style="left:78px">
  <div class="thumb" role="img" aria-label="Photo of a broker meeting an older couple at home" style="background:linear-gradient(135deg,#dfe3e6,#b8b2a8)"></div>
  <div class="meta"><i>by fletcher</i> &nbsp; | &nbsp; <i>April 21, 2016</i></div>
  <h3>Retail banks wake up to digital</h3>
  <p>know how to pursue pleasure rationally seds encounter consequences.</p>
</div>
<div class="abs card" style="left:435px">
  <div class="thumb" role="img" aria-label="Photo of a couple lying among moving boxes on a wooden floor" style="background:linear-gradient(135deg,#a98a68,#7a5d44)"></div>
  <div class="meta"><i>by fletcher</i> &nbsp; | &nbsp; <i>April 21, 2016</i></div>
  <h3>Retail banks wake up to digital</h3>
  <p>know how to pursue pleasure rationally seds encounter consequences.</p>
</div>
<div class="abs card" style="left:791px">
  <div class="thumb" role="img" aria-label="Photo of a couple relaxing on the floor of a new home with boxes" style="background:linear-gradient(135deg,#e8e6e2,#b9aa98)"></div>
  <div class="meta"><i>by fletcher</i> &nbsp; | &nbsp; <i>April 21, 2016</i></div>
  <h3>Retail banks wake up to digital</h3>
  <p>know how to pursue pleasure rationally seds encounter consequences.</p>
</div>

<!-- newsletter -->
<div class="abs news">
  <h2>Subscribe Newsletter</h2>
  <div class="email">
    <svg width="22" height="16" viewBox="0 0 22 16"><rect width="22" height="16" rx="1" fill="#333"/><path d="M1 1l10 8 10-8" fill="none" stroke="#fff" stroke-width="1.6"/></svg>
    Enter Your Email
    <span class="send"><svg width="22" height="22" viewBox="0 0 24 24"><path d="M2 11L22 2l-9 20-2-9z" fill="#fff"/></svg></span>
  </div>
</div>
<div class="abs map" role="img" aria-label="Street map showing the office location"></div>

<!-- footer -->
<div class="abs footer"></div>
<div class="abs fcol" style="left:80px;width:215px">
  <h4>About Us</h4>
  <div class="fbrand">Brightkey</div>
  <p>Suspendisse et congue nisl. Proin eros tellus, gravida sodales ipsum id, tincidunt condimentum dui cum sociis....<a>READ MORE</a></p>
</div>
<div class="abs fcol" style="left:348px">
  <h4>Navigation</h4>
  <ul><li>- Home</li><li>- About Us</li><li>- Speak to a Broker</li><li>- Articles</li><li>- Contact Us</li></ul>
</div>
<div class="abs fcol" style="left:617px">
  <h4>Get In Touch</h4>
  <div class="contact-row"><svg width="16" height="22" viewBox="0 0 16 22"><path d="M8 0a8 8 0 0 1 8 8c0 6-8 14-8 14S0 14 0 8a8 8 0 0 1 8-8z" fill="#71aa3d"/><circle cx="8" cy="8" r="3" fill="#2e2e2e"/></svg><p>Lorem Ipsum simply dummy printingtypesetting industry.</p></div>
  <div class="contact-row"><svg width="18" height="18" viewBox="0 0 24 24"><path fill="#71aa3d" d="M6.6 10.8c1.4 2.8 3.8 5.1 6.6 6.6l2.2-2.2c.3-.3.7-.4 1-.2 1.1.4 2.3.6 3.6.6.6 0 1 .4 1 1V20c0 .6-.4 1-1 1C10.6 21 3 13.4 3 4c0-.6.4-1 1-1h3.5c.6 0 1 .4 1 1 0 1.3.2 2.5.6 3.6.1.3 0 .7-.2 1l-2.3 2.2z"/></svg><p>123-456-7890</p></div>
  <div class="contact-row"><svg width="20" height="15" viewBox="0 0 22 16"><rect width="22" height="16" rx="1" fill="#71aa3d"/><path d="M1 1l10 8 10-8" fill="none" stroke="#2e2e2e" stroke-width="1.6"/></svg><p>contact@brightkeylending.com</p></div>
</div>
<div class="abs fcol" style="left:892px;width:232px">
  <h4>Contact Form</h4>
  <div class="finput" style="height:48px">Name :</div>
  <div class="finput" style="height:48px">Email :</div>
  <div class="finput" style="height:74px">Message :</div>
  <div class="btn-green" style="height:46px;border-radius:3px;margin-top:18px">SEND MESSAGE</div>
</div>
<div class="abs rule"></div>
<p class="abs copy">Copyright © <b>Brightkey Lending</b> - 2018 . All Right reserved</p>

</body>
</html>
```